Business card design needed

Our company background is that we provides transfers to and from the airport, social & corporate events, weddings.
We are also available for charter for birthday party, wine tastings, concerts, anniversary, school balls etc.
Our business cards have to reflect that we have a professional company, they are our first contact and have to stand out from the other 'players' in the market.

Industry/Entity Type

School

Contact Information for Business Card

TELVIK BDR, Lorcan & Mirabel, mob: 0428 351 972, PO Box 847, Kwinana WA 6971, ABN 52 714 309 268, Lic 7164/2918,

Requirements
Must have
• Telephone number: 0428 351 972
Website: www.TELVIKBDR.com.au
postal address: PO Box 847, Kwinana WA 6971
Licences: Lic 7164/2918

***If using the new photo (one with the bus and buildings behind it), if possible can the buildings be cropped out. Thanks
Nice to have
• would be nice to have the pics of the vehicle(s), preferred the Vorn on the card but not too fussed.
Should not have
• Picture of vehicle we don't have in our fleet. (We ONLY have the Vornelles and Korimu Daltra mini bus)

```html
<!DOCTYPE html>
<html lang="en">
<head>
<meta charset="utf-8">
<title>TELVIK BDR – Business Cards</title>
<link rel="stylesheet" href="https://fonts.googleapis.com/css2?family=Cormorant+Garamond:ital,wght@0,600;1,500&display=swap">
<style>
  :root {
    --page-bg: #e6e4e1;
    --card-dark: #0c0c0d;
    --card-mid: #1b1b1d;
    --gold: #c9a64a;
    --text-light: #d9d9d9;
    --text-muted: #b5b5b5;
    --rule: #3a3a3d;
    --photo-silver: #8f8a82;
    --photo-white: #d8dadc;
  }
  * { box-sizing: border-box; margin: 0; padding: 0; }
  html, body {
    width: 1200px; height: 900px; overflow: hidden;
    background: var(--page-bg);
  }
  body { position: relative; font-family: "Cormorant Garamond", Georgia, serif; }

  .card {
    position: absolute; left: 280px;
    width: 640px; height: 380px;
    background: linear-gradient(160deg, var(--card-mid) 0%, var(--card-dark) 60%, #070708 100%);
    box-shadow: 0 10px 28px rgba(0,0,0,.35);
    overflow: hidden;
    color: var(--text-light);
  }
  .card--front { top: 45px; }
  .card--back  { top: 475px; }

  .brand {
    position: absolute;
    font-family: "Cormorant Garamond", Georgia, serif;
    font-weight: 600; font-style: normal;
    color: var(--gold);
    font-size: 42px; line-height: 1; letter-spacing: 2px;
    white-space: nowrap;
  }

  .rule { position: absolute; left: 0; right: 0; height: 1px; background: var(--rule); }

  .photo { position: absolute; border-radius: 18px 30px 10px 10px; }
  .photo--sedan { background: linear-gradient(170deg, #b9b4ab 0%, var(--photo-silver) 55%, #4c4944 100%); }
  .photo--van   { background: linear-gradient(170deg, #f1f2f3 0%, var(--photo-white) 60%, #8d9093 100%); }

  .service { position: absolute; font-style: italic; font-weight: 500; font-size: 18px; line-height: 1.3; }
  .service__label { position: absolute; left: 0; top: 0; color: var(--text-muted); white-space: nowrap; }
  .service__list { margin-left: 100px; }

  /* front */
  .card--front .photo--sedan { left: 360px; top: 22px; width: 240px; height: 150px; }
  .card--front .rule--upper { top: 190px; }
  .card--front .rule--lower { top: 300px; }
  .card--front .brand { left: 40px; top: 224px; }
  .service--charter { left: 330px; top: 204px; width: 295px; }
  .service--transfers { left: 32px; top: 318px; width: 580px; }

  /* back */
  .card--back .brand { left: 60px; top: 100px; font-size: 46px; }
  .contact { position: absolute; left: 380px; font-style: italic; font-weight: 500; font-size: 19px; color: var(--text-light); white-space: nowrap; }
  .contact--names { top: 38px; font-size: 22px; }
  .contact--phone { top: 120px; display: flex; align-items: center; gap: 12px; }
  .contact--post { top: 200px; display: flex; align-items: flex-start; gap: 12px; font-size: 17px; line-height: 1.35; color: var(--text-muted); }
  .contact--post svg { margin-top: 3px; }
  .contact svg { flex: none; }
  .card--back .photo--sedan { left: 30px; top: 258px; width: 190px; height: 95px; }
  .card--back .photo--van   { left: 235px; top: 215px; width: 130px; height: 85px; }
</style>
</head>
<body>

<section class="card card--front" aria-label="Business card front">
  <div class="photo photo--sedan" role="img" aria-label="Photo of the silver Vorn sedan"></div>
  <div class="rule rule--upper"></div>
  <div class="service service--charter">
    <span class="service__label">Charter for:</span>
    <p class="service__list">birthday party, wine tastings, concerts, anniversary, school balls....</p>
  </div>
  <div class="brand">TELVIK BDR</div>
  <div class="rule rule--lower"></div>
  <div class="service service--transfers">
    <span class="service__label">Transfers:</span>
    <p class="service__list">to and from the airport, social &amp; corporate events, weddings....</p>
  </div>
</section>

<section class="card card--back" aria-label="Business card back">
  <div class="brand">TELVIK BDR</div>
  <p class="contact contact--names">Lorcan &amp; Mirabel</p>
  <p class="contact contact--phone">
    <svg width="12" height="18" viewBox="0 0 12 18" aria-hidden="true">
      <rect x="1" y="1" width="10" height="16" rx="2" fill="none" stroke="#d9d9d9" stroke-width="1.5"/>
      <circle cx="6" cy="14" r="1" fill="#d9d9d9"/>
    </svg>
    0428 351 972
  </p>
  <div class="contact contact--post">
    <svg width="18" height="16" viewBox="0 0 18 16" aria-hidden="true">
      <path d="M1 8 L9 1 L17 8 M3.5 6.5 V15 H14.5 V6.5" fill="none" stroke="#d9d9d9" stroke-width="1.5"/>
    </svg>
    <p>PO Box 847, Kwinana WA 6971,<br>ABN 52 714 309 268<br>Lic 7164/2918</p>
  </div>
  <div class="photo photo--sedan" role="img" aria-label="Photo of the silver Vorn sedan"></div>
  <div class="photo photo--van" role="img" aria-label="Photo of the white Korimu Daltra mini bus"></div>
</section>

</body>
</html>
```